Mastering Modern Vineyard Management

size of the ad - 8”x 10.75" plus 0.25" bleed
I would like an ad for a magazine that will stand out and make people want to read the ad.
The ad should not be crowded and people reading the ad will be able to read the text.
I would like it to be a creative and modern-day design.
the list of topics should not be the focus of the ad.
the text is attached.
If you decide to use people in the ad then please no ladies.
please note that leave over 1 inch for the bottom of the footer

```html
<!DOCTYPE html>
<html lang="en">
<head>
<meta charset="utf-8">
<title>Real Estate Course</title>
<link href="https://fonts.googleapis.com/css2?family=Anton&family=Oswald:wght@600;700&family=Roboto+Condensed:wght@400;700&family=Roboto:wght@400&display=swap" rel="stylesheet">
<style>
  :root {
    --navy: #07446d;
    --navy-text: #0d4a73;
    --sky-mid: #4c7a9b;
    --sky-light: #9db5c6;
    --mist: #d6e0e7;
    --white: #ffffff;
    --ink: #222222;
    --footer: #e3e4e5;
  }
  html, body { margin: 0; padding: 0; overflow: hidden; background: var(--white); }
  .ad {
    position: relative;
    width: 942px;
    height: 1200px;
    overflow: hidden;
    background: linear-gradient(to bottom,
      var(--navy) 0px, var(--navy) 320px,
      var(--sky-mid) 520px, var(--sky-light) 700px,
      var(--mist) 810px, var(--white) 880px, var(--white) 1115px);
  }
  .footer-band {
    position: absolute; left: 0; right: 0; top: 1115px; bottom: 0;
    background: var(--footer);
  }
  .headline { position: absolute; left: 0; top: 40px; width: 942px; height: 110px; }
  .headline text { font-family: "Anton", "Oswald", sans-serif; fill: var(--white); }
  .skyline {
    position: absolute; left: 127px; top: 166px; width: 617px; height: 524px;
    background: linear-gradient(to bottom, #2f6e9c 0%, #e6eef4 60%, #ffffff 100%);
    opacity: 0.9;
  }
  .course-title { position: absolute; left: 0; top: 708px; width: 942px; height: 44px; }
  .course-title text { font-family: "Oswald", sans-serif; font-weight: 700; fill: var(--navy-text); }
  .tagline {
    position: absolute; left: 0; top: 750px; width: 942px; margin: 0;
    text-align: center; font-family: "Roboto Condensed", sans-serif;
    font-size: 20px; color: var(--ink);
  }
  .label {
    position: absolute; margin: 0;
    font-family: "Oswald", sans-serif; font-weight: 700; font-size: 16px;
    color: var(--ink); letter-spacing: 0.2px;
  }
  .topics-label { left: 152px; top: 811px; }
  .location-label { left: 539px; top: 811px; }
  .topic-list {
    position: absolute; left: 152px; top: 838px; margin: 0; padding: 0 0 0 18px;
    font-family: "Roboto Condensed", sans-serif; font-size: 18.5px;
    color: var(--ink); line-height: 24.3px;
  }
  .topic-list li::marker { color: var(--navy-text); font-size: 16px; }
  .sessions {
    position: absolute; left: 540px; top: 834px; width: 168px; height: 78px;
    background: var(--navy); color: var(--white); padding: 5px 10px 0 10px;
    font-family: "Roboto Condensed", sans-serif;
  }
  .sessions-line { margin: 0; font-size: 17px; line-height: 21px; }
  .sessions-start { margin: 2px 0 0; font-size: 24px; line-height: 28px; }
  .perk {
    position: absolute; left: 513px; margin: 0;
    font-family: "Oswald", sans-serif; font-weight: 600; font-size: 22px;
    color: var(--navy-text); display: flex; align-items: center; gap: 6px;
  }
  .perk svg { width: 20px; height: 20px; flex: none; }
  .perk-scholarship { top: 967px; }
  .perk-earlybird { top: 1005px; }
  .audience {
    position: absolute; left: 540px; top: 1051px; margin: 0;
    font-family: "Roboto", sans-serif; font-size: 17px; line-height: 24px; color: var(--ink);
  }
</style>
</head>
<body>
<main class="ad">
  <svg class="headline" viewBox="0 0 942 110" aria-labelledby="headline-text">
    <text id="headline-text" x="71" y="98" font-size="104" textLength="799" lengthAdjust="spacingAndGlyphs">REAL ESTATE COURSE</text>
  </svg>

  <div class="skyline" role="img" aria-label="Line illustration of a city skyline with tall office towers, trees, clouds and a sun"></div>

  <svg class="course-title" viewBox="0 0 942 44" aria-labelledby="course-title-text">
    <text id="course-title-text" x="135" y="37" font-size="33" textLength="672" lengthAdjust="spacingAndGlyphs">MASTERING MODERN VINEYARD MANAGEMENT</text>
  </svg>
  <p class="tagline">Investing in knowledge is investing in opportunities.</p>

  <p class="label topics-label">TOPICS:</p>
  <ul class="topic-list">
    <li>Partial listing</li>
    <li>Real estate investment strategies</li>
    <li>Due diligence</li>
    <li>Financing</li>
    <li>Underwriting</li>
    <li>Property management</li>
    <li>Real estate Legal basics</li>
    <li>Sourcing deals</li>
    <li>Syndication</li>
    <li>Dealing with brokers</li>
    <li>Tax fundamentals</li>
  </ul>

  <p class="label location-label">ASHFORD VALE</p>
  <div class="sessions">
    <p class="sessions-line">10 -TUESDAY</p>
    <p class="sessions-line">EVENINGS SESSIONS</p>
    <p class="sessions-start">Starting Feb.28</p>
  </div>

  <p class="perk perk-scholarship">
    <svg viewBox="0 0 20 20" aria-hidden="true"><path d="M2 11 L8 17 L18 3" fill="none" stroke="#0d4a73" stroke-width="3" stroke-linecap="round" stroke-linejoin="round"/></svg>
    Limited Partial Scholarships
  </p>
  <p class="perk perk-earlybird">
    <svg viewBox="0 0 20 20" aria-hidden="true"><path d="M2 11 L8 17 L18 3" fill="none" stroke="#0d4a73" stroke-width="3" stroke-linecap="round" stroke-linejoin="round"/></svg>
    Early Bird Special
  </p>
  <p class="audience">For those that started or<br>would like to go into real estate</p>

  <div class="footer-band"></div>
</main>
</body>
</html>
```